Irrigation Business needs their business cards modernised and revamped

I would like to keep my current logo, colours and revamp the format of the card.

I would like the card to be clean yet important.

Im not sure if you include texture but i would like the named logo to be indented into the card etc.

show me something alive and free something thats clinical to the point yet has a feel of achievement. i would like people to go nice card.

Target Market(s)

high end clients, corporate, sports field manger, the guys that make the decisions

Industry/Entity Type

Business

Contact Information for Business Card

nformation to be included

Dean Harlow (Director)
0487305526
dean@kolvat.biz
www.kestonfieldworks.com

instagram logo
google logo
facebook logo

Colors

Designer to choose colors to be used in the design.

Requirements
Nice to have
• indentations a really nice feel to the card good texture

```html
<!DOCTYPE html>
<html lang="en">
<head>
<meta charset="utf-8">
<title>Keston Fieldworks – Business Card</title>
<link href="https://fonts.googleapis.com/css2?family=Roboto:wght@400;700&family=Roboto+Condensed:wght@700&display=swap" rel="stylesheet">
<style>
  :root {
    --backdrop: #2a2a2a;
    --card: #f1f1f1;
    --brand-blue: #2c63a8;
    --brand-green: #279a50;
    --sky-blue: #33a6d6;
    --white: #ffffff;
    --rule: #a9a9a9;
  }
  * { margin: 0; padding: 0; box-sizing: border-box; }
  html, body { width: 1200px; height: 960px; overflow: hidden; }
  body {
    background: var(--backdrop);
    font-family: "Roboto", Arial, sans-serif;
    position: relative;
  }
  .card {
    position: absolute;
    width: 600px;
    height: 343px;
    background: var(--card);
    box-shadow: 0 3px 8px rgba(0,0,0,.5);
  }
  .card-front { left: 314px; top: 113px; }
  .card-back { left: 311px; top: 472px; }

  .wordmark {
    position: absolute;
    left: 0; right: 0;
    text-align: center;
    color: var(--brand-blue);
    font-weight: 700;
    font-size: 34px;
    letter-spacing: -0.5px;
    line-height: 1;
  }
  .card-front .wordmark { top: 72px; }
  .card-back .wordmark { top: 196px; }

  .info-band {
    position: absolute;
    left: 0; right: 0;
    top: 200px;
    height: 108px;
    background: linear-gradient(90deg, var(--brand-blue) 0 53%, var(--brand-green) 53% 100%);
  }
  .brand-disc {
    position: absolute;
    border-radius: 50%;
    background: var(--sky-blue);
  }
  .card-front .brand-disc {
    left: 243px; top: -3px;
    width: 114px; height: 114px;
    border: 3px solid var(--white);
    box-shadow: 0 0 0 3px var(--brand-blue);
  }
  .card-back .brand-disc {
    left: 247px; top: 80px;
    width: 106px; height: 106px;
    border: 4px solid var(--brand-blue);
  }
  .person {
    position: absolute;
    left: 31px; top: 31px;
    color: var(--white);
  }
  .person-name {
    font-family: "Roboto Condensed", "Arial Narrow", sans-serif;
    font-weight: 700;
    font-size: 21px;
    line-height: 1;
  }
  .person-role {
    font-size: 14px;
    font-weight: 400;
    margin-top: 6px;
    letter-spacing: .3px;
  }
  .contact {
    position: absolute;
    right: 19px; top: 27px;
    list-style: none;
    color: var(--white);
    font-size: 14.5px;
    text-align: right;
  }
  .contact li {
    display: flex;
    justify-content: flex-end;
    align-items: center;
    gap: 6px;
    height: 19px;
  }
  .contact svg { width: 13px; height: 13px; fill: var(--white); }

  .social-row {
    position: absolute;
    left: 34px; right: 30px;
    top: 291px;
    display: flex;
    align-items: center;
    gap: 4px;
  }
  .social-row .rule {
    flex: 1;
    height: 2px;
    background: linear-gradient(90deg, transparent, var(--rule) 40%, var(--rule));
  }
  .social-row .rule:last-child {
    background: linear-gradient(90deg, var(--rule), var(--rule) 60%, transparent);
  }
  .social-dot {
    width: 29px; height: 29px;
    border-radius: 50%;
    background: var(--brand-blue);
  }
</style>
</head>
<body>
  <section class="card card-front">
    <div class="wordmark">KESTON FIELDWORKS</div>
    <div class="info-band">
      <div class="person">
        <div class="person-name">DEAN HARLOW</div>
        <div class="person-role">DIRECTOR</div>
      </div>
      <div class="brand-disc"></div>
      <ul class="contact">
        <li>0487305526
          <svg viewBox="0 0 16 16"><path d="M3.6 1.2l2.3 2.6-1.3 2a9 9 0 0 0 5.6 5.6l2-1.3 2.6 2.3-1.4 2.2C8 14.8 1.2 8 .8 2.6z"/></svg>
        </li>
        <li>dean@kolvat.biz
          <svg viewBox="0 0 16 16"><path d="M1 3h14v10H1zM2.5 4.5 8 9l5.5-4.5v-.5h-11z" fill-rule="evenodd"/></svg>
        </li>
        <li>kestonfieldworks.com
          <svg viewBox="0 0 16 16"><path d="M8 1a7 7 0 1 0 0 14A7 7 0 0 0 8 1zm0 2a5 5 0 0 1 3.5 1.4c-.6.3-1.3.2-1.8.8-.5.6 0 1.5-.6 2-.7.4-1.6-.4-2.2.2-.6.6 0 1.6.5 2.2.5.7.3 1.7-.3 2.4A5 5 0 0 1 8 3z"/></svg>
        </li>
      </ul>
    </div>
  </section>

  <section class="card card-back">
    <div class="brand-disc"></div>
    <div class="wordmark">KESTON FIELDWORKS</div>
    <div class="social-row">
      <span class="rule"></span>
      <span class="social-dot"></span>
      <span class="social-dot"></span>
      <span class="social-dot"></span>
      <span class="rule"></span>
    </div>
  </section>
</body>
</html>
```